Business card design needed

Business Card design required for new small plumbing business.
Would like a logo/text look that is simple and unique and does not have to be representative of a plumbing company (ie. having a cartoon plumber or toilet etc) as the companyname is self explanatory.
Would like the main colour to be green (lime green).

Industry/Entity Type

Plumber

Contact Information for Business Card

BRAMFORD PLUMBING
ABN 71 546 190 327 004

Simon Harcastle
Licensed Plumber 83615
Phone: 0487 214 670

27 Bramford Drive,
Kelmsworth. 4021 Westland

Email: bramfordplumbing@quellmail.example

Logo Text

Bramford Plumbing

Logo styles of interest
Character Logo
Wordmark Logo
Lettermark Logo

```html
<!DOCTYPE html>
<html lang="en">
<head>
<meta charset="utf-8">
<title>Bramford Plumbing – Business Card</title>
<link rel="stylesheet" href="https://fonts.googleapis.com/css2?family=Source+Sans+3:wght@400;600;700&display=swap">
<style>
  :root {
    --lime: #b5d566;
    --slate: #6b6d6a;
    --edge: #c9c9c9;
    --paper: #ffffff;
  }
  * { margin: 0; padding: 0; box-sizing: border-box; }
  html, body {
    width: 1200px; height: 559px; overflow: hidden;
    background: var(--paper);
    font-family: "Source Sans 3", "Myriad Pro", sans-serif;
  }
  .stage { position: relative; width: 1200px; height: 559px; }
  .card {
    position: absolute; top: 122px;
    width: 549px; height: 318px;
    border: 1px solid var(--edge);
    background: var(--paper);
    overflow: hidden;
  }
  .card--front { left: 35px; }
  .card--back { left: 618px; }

  .brand {
    position: absolute; display: flex; align-items: flex-end;
    color: var(--lime); font-weight: 600; white-space: nowrap;
  }
  .brand__dot { background: var(--lime); flex: none; }
  .brand__name { display: block; line-height: 0.8; }
  .card--front .brand { left: 97px; top: 136px; font-size: 35px; gap: 10px; }
  .card--front .brand__dot { width: 40px; height: 40px; }
  .card--back .brand { left: 34px; top: 51px; font-size: 18px; gap: 7px; }
  .card--back .brand__dot { width: 20px; height: 20px; }

  .details {
    position: absolute; left: 33px; top: 97px; right: 0; bottom: 0;
    background: var(--lime);
    color: var(--slate);
    text-align: right;
    padding: 27px 31px 0 0;
  }
  .details__name { font-size: 40px; font-weight: 700; line-height: 1; letter-spacing: 0.3px; }
  .details__role { font-size: 16px; font-weight: 400; margin-top: 8px; line-height: 1; }
  .details__contact { font-size: 17px; font-weight: 600; line-height: 21px; margin-top: 11px; }
  .details__address { font-size: 15px; font-weight: 400; line-height: 20px; margin-top: 16px; }
</style>
</head>
<body>
<main class="stage">
  <section class="card card--front">
    <div class="brand"><span class="brand__dot"></span><span class="brand__name">BRAMFORD PLUMBING</span></div>
  </section>

  <section class="card card--back">
    <div class="brand"><span class="brand__dot"></span><span class="brand__name">BRAMFORD PLUMBING</span></div>
    <div class="details">
      <h1 class="details__name">Simon Harcastle</h1>
      <p class="details__role">-&nbsp; Licensed Plumber</p>
      <p class="details__contact">0487 214 670 27 83615<br>bramfordplumbing@quellmail.example</p>
      <p class="details__address">Bramford Drive, Kelmsworth. 4021 Westland<br>ABN 71 546 190 327 004</p>
    </div>
  </section>
</main>
</body>
</html>
```